Ward Compass Business Card Design*

We need a business card design for our company Ward Compass. Our company is specialized in providing online consulting services regarding medical institutions, hospitals and doctors. We work with patients worldwide looking to choose between healthcare providers. We have a website you may use as a reference, where we list doctors and clinics worldwide. So we target Medical providers as well as patients worldwide.
Target Market(s)
Medical Providers and patients around the world
Industry/Entity Type
Medical
Contact Information for Business Card
Salwa Kettani
CEO
+90 612 348 2175
info@wardcompass.example
www.wardcompass.example
14 Annakhil 7 H.R.B. Rabat, Morocco
Requirements
Must have
- Company logo/name on one full side, personal info and smaller logo and company name on the other side.
Nice to have
- Smart and elegant design

```html
<!DOCTYPE html>
<html lang="en">
<head>
<meta charset="utf-8">
<title>Ward Compass – Business Card</title>
<link href="https://fonts.googleapis.com/css2?family=Quicksand:wght@400;500;700&display=swap" rel="stylesheet">
<style>
  :root {
    --bg: #141414;
    --card: #2a2b2b;
    --silver: #d2d2d2;
    --silver-dim: #9a9a9a;
    --rule: #8c8c8c;
  }
  * { box-sizing: border-box; margin: 0; padding: 0; }
  html, body { width: 1200px; height: 900px; overflow: hidden; }
  body {
    background: var(--bg);
    font-family: "Quicksand", sans-serif;
    color: var(--silver);
    display: flex;
    flex-direction: column;
    align-items: center;
    justify-content: center;
    gap: 60px;
  }
  .card {
    width: 600px;
    height: 340px;
    background: var(--card);
    border-radius: 4px;
    position: relative;
  }
  /* Front side */
  .card-front {
    display: flex;
    align-items: center;
    justify-content: center;
  }
  .front-name {
    font-weight: 500;
    font-size: 40px;
    letter-spacing: 0.12em;
    color: var(--silver);
    text-transform: uppercase;
  }
  /* Back side */
  .card-back { padding: 0 40px; }
  .brand {
    position: absolute;
    left: 40px;
    top: 118px;
    display: flex;
    align-items: center;
    gap: 12px;
  }
  .brand-dot {
    width: 22px; height: 22px;
    border-radius: 50%;
    background: var(--silver);
  }
  .brand-name {
    font-weight: 500;
    font-size: 21px;
    letter-spacing: 0.1em;
    text-transform: uppercase;
    color: var(--silver);
  }
  .divider {
    position: absolute;
    left: 318px;
    top: 80px;
    width: 1px;
    height: 140px;
    background: var(--rule);
  }
  .person {
    position: absolute;
    left: 338px;
    top: 82px;
  }
  .person-name { font-size: 20px; font-weight: 400; color: var(--silver); }
  .person-name strong { font-weight: 700; }
  .person-role { font-size: 13px; color: var(--silver-dim); margin-top: 2px; }
  .contacts { list-style: none; margin-top: 12px; }
  .contacts li {
    display: flex;
    align-items: center;
    gap: 9px;
    font-size: 13.5px;
    line-height: 22px;
    color: var(--silver);
  }
  .contacts svg { width: 12px; height: 12px; flex: none; }
  .address {
    position: absolute;
    left: 40px;
    bottom: 34px;
    font-size: 13px;
    color: var(--silver-dim);
  }
</style>
</head>
<body>
  <section class="card card-front" aria-label="Card front">
    <span class="front-name">Ward Compass</span>
  </section>

  <section class="card card-back" aria-label="Card back">
    <div class="brand">
      <span class="brand-dot"></span>
      <span class="brand-name">Ward Compass</span>
    </div>
    <div class="divider"></div>
    <div class="person">
      <p class="person-name"><strong>Salwa</strong> Kettani</p>
      <p class="person-role">CEO</p>
      <ul class="contacts">
        <li>
          <svg viewBox="0 0 12 12" aria-hidden="true"><path d="M2.5 1 L4.5 1 L5 3.5 L3.8 4.4 Q4.8 6.8 7.6 8.2 L8.5 7 L11 7.5 L11 9.5 Q10.5 11 9 11 Q1 10 1 2.5 Q1 1 2.5 1 Z" fill="#d2d2d2"/></svg>
          +90 612 348 2175
        </li>
        <li>
          <svg viewBox="0 0 12 12" aria-hidden="true"><rect x="0.6" y="2.2" width="10.8" height="7.6" fill="none" stroke="#d2d2d2" stroke-width="1.1"/><path d="M0.8 2.5 L6 6.6 L11.2 2.5" fill="none" stroke="#d2d2d2" stroke-width="1.1"/></svg>
          info@wardcompass.example
        </li>
        <li>
          <svg viewBox="0 0 12 12" aria-hidden="true"><circle cx="6" cy="6" r="5.3" fill="none" stroke="#d2d2d2" stroke-width="1.1"/><ellipse cx="6" cy="6" rx="2.2" ry="5.3" fill="none" stroke="#d2d2d2" stroke-width="1"/><path d="M0.7 6 H11.3" stroke="#d2d2d2" stroke-width="1"/></svg>
          www.wardcompass.example
        </li>
      </ul>
    </div>
    <p class="address">14 Annakhil, 7 H.R.B., Rabat, Morocco</p>
  </section>
</body>
</html>
```